Profesional personal website needs design and business card

I need a business card with my professional name as a logo "Dorian Vitality" for my business. I am a Wellness Coach, consultant and trainer. So it should be professional, wellness oriented and modern.

Target Market(s)

Private clients, governments, corporations. Luxury and high market.

Industry/Entity Type

Health And Wellness

Contact Information for Business Card

Dorian Vitality should be the logo

Colors

Designer to choose colors to be used in the design.

Requirements
Must have
• Dorian Vitality
• Name: Tomás Lirandel
• Wellness Coach, Consultant & Trainer.
• Website: www.dorianvitality-example.com
• Phone:
• Spain (+34) 612 480 317
• (USA) +1 (555) 610 4829
Nice to have
• The most important is the design of "Dorian Vitality", as this is going to be my personal brand logo. It should be professional, wellness, high end and actual.
Should not have
• no golds, no baroque style..

```html
<!DOCTYPE html>
<html lang="en">
<head>
<meta charset="utf-8">
<title>Dorian Vitality – Business Card</title>
<link href="https://fonts.googleapis.com/css2?family=Montserrat:wght@400;500;700;800&display=swap" rel="stylesheet">
<style>
  :root {
    --backdrop: #1e1e1e;
    --card-blue: #1b1fb3;
    --card-blue-deep: #161a9c;
    --accent-yellow: #f6c400;
    --text-white: #ffffff;
    --emboss-blue: #3a3fc4;
    --flag-red: #c8102e;
    --flag-gold: #ffc400;
    --flag-navy: #2a3a7a;
  }
  * { box-sizing: border-box; margin: 0; padding: 0; }
  html, body { width: 1200px; height: 900px; overflow: hidden; }
  body {
    background: var(--backdrop);
    font-family: "Montserrat", sans-serif;
    display: flex;
    flex-direction: column;
    align-items: center;
    justify-content: center;
    gap: 36px;
  }
  .card {
    width: 700px;
    height: 400px;
    background: linear-gradient(135deg, var(--card-blue) 0%, var(--card-blue-deep) 100%);
    border-bottom: 6px solid var(--accent-yellow);
    position: relative;
    box-shadow: 0 10px 30px rgba(0,0,0,0.5);
  }
  /* Back side */
  .card--back {
    display: flex;
    align-items: center;
    justify-content: center;
  }
  .brand-mark--emboss {
    font-weight: 800;
    font-size: 58px;
    letter-spacing: 2px;
    text-transform: uppercase;
    color: var(--emboss-blue);
  }
  /* Front side */
  .card--front {
    display: flex;
    align-items: center;
    padding: 0 40px 0 56px;
  }
  .brand-block {
    width: 270px;
    display: flex;
    align-items: center;
  }
  .brand-mark {
    font-weight: 800;
    font-size: 38px;
    line-height: 1.05;
    text-transform: uppercase;
    color: var(--text-white);
  }
  .divider {
    width: 2px;
    height: 190px;
    background: var(--accent-yellow);
    margin: 0 36px 0 20px;
  }
  .contact-block { color: var(--text-white); flex: 1; }
  .person-name {
    font-weight: 700;
    font-size: 24px;
    letter-spacing: 1px;
    color: var(--accent-yellow);
    text-transform: uppercase;
  }
  .person-role {
    font-size: 15px;
    line-height: 1.3;
    margin: 4px 0 16px;
  }
  .contact-list { list-style: none; font-size: 14.5px; line-height: 1.75; }
  .contact-item { display: flex; align-items: center; gap: 10px; }
  .contact-item svg { width: 14px; height: 14px; flex: none; }
  .contact-item .flag { margin-left: auto; width: 26px; height: 16px; }
  .web-highlight { color: var(--accent-yellow); }
</style>
</head>
<body>
  <section class="card card--back" aria-label="Card back">
    <div class="brand-mark--emboss">Dorian Vitality</div>
  </section>

  <section class="card card--front" aria-label="Card front">
    <div class="brand-block">
      <div class="brand-mark">Dorian<br>Vitality</div>
    </div>
    <div class="divider"></div>
    <div class="contact-block">
      <h1 class="person-name">Tomás Lirandel</h1>
      <p class="person-role">Wellness Coach,<br>Consultant &amp; Trainer</p>
      <ul class="contact-list">
        <li class="contact-item">
          <svg viewBox="0 0 16 16"><path d="M4 1l3 3-2 2c1 2 3 4 5 5l2-2 3 3-2 2C7 14 2 9 2 3z" fill="none" stroke="var(--accent-yellow)" stroke-width="1.5"/></svg>
          <span>(+34) 612 480 317</span>
          <svg class="flag" viewBox="0 0 26 16"><rect width="26" height="16" fill="var(--flag-red)"/><rect y="4" width="26" height="8" fill="var(--flag-gold)"/></svg>
        </li>
        <li class="contact-item">
          <svg viewBox="0 0 16 16"><rect x="4" y="1" width="8" height="14" rx="1.5" fill="none" stroke="var(--accent-yellow)" stroke-width="1.5"/><circle cx="8" cy="12.5" r="0.9" fill="var(--accent-yellow)"/></svg>
          <span>+1 (555) 610 4829</span>
          <svg class="flag" viewBox="0 0 26 16"><rect width="26" height="16" fill="#fff"/><g fill="var(--flag-red)"><rect width="26" height="2"/><rect y="4" width="26" height="2"/><rect y="8" width="26" height="2"/><rect y="12" width="26" height="2"/></g><rect width="11" height="8" fill="var(--flag-navy)"/></svg>
        </li>
        <li class="contact-item">
          <svg viewBox="0 0 16 16"><rect x="1.5" y="3.5" width="13" height="9" fill="none" stroke="var(--accent-yellow)" stroke-width="1.4"/><path d="M1.5 3.5l6.5 5 6.5-5" fill="none" stroke="var(--accent-yellow)" stroke-width="1.4"/></svg>
          <span>info@dorianvitality-example.com</span>
        </li>
        <li class="contact-item">
          <svg viewBox="0 0 16 16"><g fill="none" stroke="var(--accent-yellow)" stroke-width="1.3"><circle cx="8" cy="8" r="6.5"/><ellipse cx="8" cy="8" rx="3" ry="6.5"/><path d="M1.5 8h13M2.5 4.5h11M2.5 11.5h11"/></g></svg>
          <span>www.<span class="web-highlight">dorianvitality-example</span>.com</span>
        </li>
      </ul>
    </div>
  </section>
</body>
</html>
```